Luxury Wine Label for New Startup Winery

We need a wine label for our new winery startup. We have worked with a local designer but do not feel the resulting label / logo have the elevation required to present our brand as a luxury wine. Our winery is called "Quailbrook Vineyards" and we are focused on extremely high quality hand crafted artisan and estate wines from the Pacific Northwest.
We would like to see designs that utilize a tree line, or other imagery that represents the "Quailbrook" part of our company name. Another interesting feature could be wood grain.
A logo will be required based on your design so please design with this in mind:
This logo should be consistent with the wine bottle label design, and should be representative of our high end exclusive wine while giving a sense of place (Oregon/ Pacific Northwest.)
I will supply an image of the design we received from our local designer, PLEASE NOTE: in general we do like wood grain and tree line concepts but feel the execution was poorly done.
ATTN: Logo design should be suitable for use on: Bottles (Red wine/rose/white wine), Bussiness cards, vehicle signage, business signage, etc
P.S.:
If you have a design that is not outside the box we are still interested in seeing it.
Label is for a burgundy style bottle with a label height of 3.5 - 4" and a width of 3.5-4"
any label <= 4"x4" and >=3.5"x3.5" will be acceptable:
HOWEVER Width should be greater than or equal to height due to the bottle format
Target Market(s)
Wine enthusiasts with adequate discretionary budgets to afford $100 bottles of wine.
Industry/Entity Type
Wine / Winery
Requirements
Must have
- A sense of luxury, a feel of exclusivity, and a theme consistent with our product and brand name
Nice to have
- Tree line, wood grain or other wood themes. Serif fonts
Should not have
- anything cheesy, off topic, hard to read script fonts or anything that makes the label hard to read from a few feet away or too busy

```html
<!DOCTYPE html>
<html lang="en">
<head>
<meta charset="utf-8">
<title>Quailbrook Vineyards — Wine Labels</title>
<link rel="stylesheet" href="https://fonts.googleapis.com/css2?family=Cormorant+Garamond:wght@500;600&family=Cinzel:wght@400;500&display=swap">
<style>
  :root {
    --stage: #2b2c2e;
    --ink-dark: #141414;
    --ink-dark-2: #1e1e1f;
    --gold: #c9a85a;
    --gold-soft: #a98a45;
    --rule-dark: #4a4a4a;
    --paper: #f4f2f1;
    --paper-shade: #e8dcdc;
    --crimson: #b43247;
    --rose-ink: #8c5a5e;
    --wood-dark-a: #2e1f16;
    --wood-dark-b: #5a3c28;
    --wood-rose-a: #6e3f33;
    --wood-rose-b: #a0665a;
    --cream: #f3ead8;
  }
  * { box-sizing: border-box; margin: 0; padding: 0; }
  html, body { width: 1200px; height: 900px; overflow: hidden; background: var(--stage); }
  .stage {
    position: relative; width: 1200px; height: 900px;
    display: flex; justify-content: center; align-items: center; gap: 60px;
  }
  .label { position: relative; width: 420px; height: 420px; }
  .label__panel { position: absolute; left: 0; top: 0; width: 420px; height: 300px; }
  .label__panel svg { display: block; }
  .label__content {
    position: absolute; left: 0; top: 0; width: 420px; height: 300px;
    display: flex; flex-direction: column; align-items: center;
  }
  .wordmark {
    margin-top: 118px;
    font-family: "Cormorant Garamond", Georgia, serif;
    font-weight: 600; font-size: 58px; line-height: 1; letter-spacing: 0.01em;
  }
  .subline {
    display: flex; align-items: center; gap: 10px; margin-top: 6px;
    font-family: "Cinzel", Georgia, serif; font-size: 13px; letter-spacing: 0.42em;
  }
  .subline::before, .subline::after { content: ""; width: 38px; height: 1px; background: currentColor; opacity: .7; }
  .region {
    margin-top: 20px;
    font-family: "Cinzel", Georgia, serif; font-size: 10px; letter-spacing: 0.32em;
  }
  .label__band {
    position: absolute; left: 0; top: 312px; width: 420px; height: 108px;
    border-radius: 4px; overflow: hidden;
  }
  .band__grain { position: absolute; inset: 0; }
  .band__rule { position: absolute; left: 30px; right: 30px; height: 1px; }
  .band__rule--top { top: 14px; }
  .band__rule--bottom { bottom: 14px; }
  .band__text {
    position: absolute; inset: 0; display: flex; flex-direction: column;
    align-items: center; justify-content: center; gap: 8px;
  }
  .varietal { font-family: "Cinzel", Georgia, serif; font-size: 34px; letter-spacing: 0.28em; padding-left: .28em; line-height: 1; }
  .meta { font-family: "Cormorant Garamond", Georgia, serif; font-weight: 600; font-size: 13px; letter-spacing: 0.12em; }

  /* Syrah */
  .label--syrah .wordmark, .label--syrah .subline, .label--syrah .region { color: var(--gold); }
  .label--syrah .band__grain { background: linear-gradient(100deg, var(--wood-dark-a), var(--wood-dark-b) 45%, var(--wood-dark-a) 70%, var(--wood-dark-b)); }
  .label--syrah .band__rule { background: var(--gold-soft); }
  .label--syrah .varietal, .label--syrah .meta { color: var(--gold); }

  /* Rosé */
  .label--rose .wordmark { color: var(--crimson); }
  .label--rose .subline, .label--rose .region { color: var(--rose-ink); }
  .label--rose .band__grain { background: linear-gradient(100deg, var(--wood-rose-a), var(--wood-rose-b) 45%, var(--wood-rose-a) 70%, var(--wood-rose-b)); }
  .label--rose .band__rule { background: var(--cream); opacity: .8; }
  .label--rose .varietal, .label--rose .meta { color: var(--cream); }
</style>
</head>
<body>
<main class="stage">

  <section class="label label--syrah" aria-label="Syrah label">
    <div class="label__panel">
      <svg width="420" height="300" viewBox="0 0 420 300">
        <defs>
          <linearGradient id="hills-dark" x1="0" y1="0" x2="0" y2="1">
            <stop offset="0" stop-color="#2a2a2b"/>
            <stop offset="1" stop-color="#1a1a1b"/>
          </linearGradient>
        </defs>
        <polygon points="0,0 420,0 420,250 210,300 0,250" fill="var(--ink-dark)"/>
        <rect x="0" y="40" width="420" height="110" fill="url(#hills-dark)" role="img" aria-label="Soft rolling hills backdrop"/>
        <line x1="24" y1="26" x2="396" y2="26" stroke="var(--rule-dark)" stroke-width="1"/>
        <polyline points="24,232 210,276 396,232" fill="none" stroke="var(--rule-dark)" stroke-width="1"/>
      </svg>
    </div>
    <div class="label__content">
      <h1 class="wordmark">Quailbrook</h1>
      <p class="subline">VINEYARDS</p>
      <p class="region">WILLAMETTE VALLEY</p>
    </div>
    <div class="label__band">
      <div class="band__grain" role="img" aria-label="Dark walnut wood grain"></div>
      <span class="band__rule band__rule--top"></span>
      <span class="band__rule band__rule--bottom"></span>
      <div class="band__text">
        <p class="varietal">SYRAH</p>
        <p class="meta">ESTATE | 2023 | GROWN</p>
      </div>
    </div>
  </section>

  <section class="label label--rose" aria-label="Rosé label">
    <div class="label__panel">
      <svg width="420" height="300" viewBox="0 0 420 300">
        <defs>
          <linearGradient id="hills-light" x1="0" y1="0" x2="0" y2="1">
            <stop offset="0" stop-color="#f4f2f1"/>
            <stop offset="1" stop-color="#e6d6d6"/>
          </linearGradient>
        </defs>
        <polygon points="0,0 420,0 420,250 210,300 0,250" fill="var(--paper)"/>
        <rect x="0" y="40" width="420" height="110" fill="url(#hills-light)" role="img" aria-label="Soft rolling hills backdrop"/>
        <line x1="24" y1="26" x2="396" y2="26" stroke="#b9a9a9" stroke-width="1"/>
        <polyline points="24,232 210,276 396,232" fill="none" stroke="#b9a9a9" stroke-width="1"/>
      </svg>
    </div>
    <div class="label__content">
      <h1 class="wordmark">Quailbrook</h1>
      <p class="subline">VINEYARDS</p>
      <p class="region">WILLAMETTE VALLEY</p>
    </div>
    <div class="label__band">
      <div class="band__grain" role="img" aria-label="Warm rosewood grain"></div>
      <span class="band__rule band__rule--top"></span>
      <span class="band__rule band__rule--bottom"></span>
      <div class="band__text">
        <p class="varietal">ROSÉ</p>
        <p class="meta">ESTATE | 2023 | GROWN</p>
      </div>
    </div>
  </section>

</main>
</body>
</html>
```